Glass Fabricator Presentation Folders

We need a folder to hold information about our company. We fabricate, laminate, temper, and digitally print any design on glass. All of this is done under one roof in our 80,000 square foot facility. Our digital printing is done by Vorn Lume technology, and is the first digital printer in the Southeastern United States. Our customers consist of commercial glaziers, architects, and designers. I have attached our existing logo.

Industry/Entity Type

It Company

Contact Information for Business Card

Harlow Pane Works, LLC
2380NW 42nd Avenue
Pompano Beach, Florida 33069
Phone: 555-615-3871
Fax:555-615-3902
www.harlowpane.example

```html
<!DOCTYPE html>
<html lang="en">
<head>
<meta charset="utf-8">
<title>Harlow Pane Works, LLC — Folder and Business Cards</title>
<link href="https://fonts.googleapis.com/css2?family=Open+Sans:wght@400;700&display=swap" rel="stylesheet">
<style>
  :root {
    --backdrop: #e8e8e8;
    --brand-blue: #2b6a9b;
    --brand-navy: #2e3277;
    --paper: #f7f7f7;
    --ink-white: #ffffff;
    --ink-blue: #2b5f94;
    --ink-navy-text: #e6e8f5;
    --mark-on-navy: #2b6a9b;
    --mark-on-blue: #ffffff;
  }
  * { box-sizing: border-box; margin: 0; padding: 0; }
  html, body {
    width: 1200px; height: 794px; overflow: hidden;
    background: var(--backdrop);
    font-family: "Open Sans", Arial, sans-serif;
  }
  .canvas { position: relative; width: 1200px; height: 794px; }

  /* Folder cover */
  .folder {
    position: absolute; left: 240px; top: 80px;
    width: 720px; height: 390px;
    background: var(--brand-blue);
    box-shadow: 0 6px 16px rgba(0,0,0,.12);
    display: flex; align-items: center; justify-content: center;
  }
  .wordmark { display: flex; align-items: center; gap: 16px; color: var(--ink-white); font-weight: 700; }
  .wordmark-square { background: currentColor; flex: none; }
  .wordmark-name { display: flex; flex-direction: column; line-height: 1; letter-spacing: .04em; text-transform: uppercase; }
  .folder .wordmark-square { width: 70px; height: 70px; }
  .folder .wordmark-main { font-size: 50px; }
  .folder .wordmark-sub { font-size: 24px; margin-top: 6px; letter-spacing: .12em; }

  /* Business cards */
  .card {
    position: absolute; width: 340px; height: 200px;
    box-shadow: 0 4px 10px rgba(0,0,0,.14);
    overflow: hidden;
  }
  .card-navy { left: 300px; top: 520px; background: var(--brand-navy); }
  .card-navy .card-band { position: absolute; left: 0; top: 0; width: 100%; height: 56px; background: var(--brand-blue); }
  .card-light { left: 680px; top: 500px; background: var(--paper); }
  .card-light .card-panel { position: absolute; right: 0; top: 0; width: 140px; height: 100%; background: var(--brand-blue); }

  .card .wordmark { position: absolute; left: 18px; top: 16px; gap: 6px; }
  .card-navy .wordmark { color: var(--ink-white); }
  .card-light .wordmark { color: var(--ink-blue); }
  .card .wordmark-square { width: 20px; height: 20px; }
  .card .wordmark-main { font-size: 15px; }
  .card .wordmark-sub { font-size: 7.5px; margin-top: 2px; letter-spacing: .1em; }

  .card-decor-square { position: absolute; width: 90px; height: 90px; }
  .card-navy .card-decor-square { left: 200px; top: 72px; background: var(--mark-on-navy); }
  .card-light .card-decor-square { right: 25px; top: 55px; background: var(--mark-on-blue); }

  .card-contact { position: absolute; left: 22px; top: 76px; font-size: 9.5px; line-height: 1.3; font-style: normal; white-space: nowrap; }
  .card-navy .card-contact { color: var(--ink-navy-text); }
  .card-light .card-contact { color: var(--ink-blue); }
  .card-contact .phones { margin-top: 18px; }
  .card-contact .web { margin-top: 18px; }
</style>
</head>
<body>
<main class="canvas">

  <section class="folder" aria-label="Presentation folder cover">
    <div class="wordmark">
      <span class="wordmark-square"></span>
      <span class="wordmark-name">
        <span class="wordmark-main">Harlow Pane</span>
        <span class="wordmark-sub">Works, LLC</span>
      </span>
    </div>
  </section>

  <article class="card card-navy" aria-label="Business card, navy">
    <div class="card-band"></div>
    <div class="wordmark">
      <span class="wordmark-square"></span>
      <span class="wordmark-name">
        <span class="wordmark-main">Harlow Pane</span>
        <span class="wordmark-sub">Works, LLC</span>
      </span>
    </div>
    <div class="card-decor-square"></div>
    <address class="card-contact">
      <div>2380NW 42nd Avenue<br>Larkmoor Bay Florida 34712</div>
      <div class="phones">P: 555-615-3871<br>F: 555-615-3902</div>
      <div class="web">www.harlowpane.example</div>
    </address>
  </article>

  <article class="card card-light" aria-label="Business card, white">
    <div class="card-panel"></div>
    <div class="wordmark">
      <span class="wordmark-square"></span>
      <span class="wordmark-name">
        <span class="wordmark-main">Harlow Pane</span>
        <span class="wordmark-sub">Works, LLC</span>
      </span>
    </div>
    <div class="card-decor-square"></div>
    <address class="card-contact">
      <div>2380NW 42nd Avenue<br>Larkmoor Bay Florida 34712</div>
      <div class="phones">P: 555-615-3871<br>F: 555-615-3902</div>
      <div class="web">www.harlowpane.example</div>
    </address>
  </article>

</main>
</body>
</html>
```